Business Cards - New Logo Rebranding

Hello We know have a red and blue logo and are looking to create new cards. We are looking for the best creativity of the new logo merged with some of the existing artwork provided.

Target Market(s)

Realtors

Industry/Entity Type

Real Estate

Contact Information for Business Card

New logo with rebranded colors

Requirements
Must have
• Creative use of the new logo

```html
<!DOCTYPE html>
<html lang="en">
<head>
<meta charset="utf-8">
<title>Keystone Group – Business Card</title>
<link rel="stylesheet" href="https://fonts.googleapis.com/css2?family=Open+Sans:wght@700&family=Roboto:wght@400;500;700;900&display=swap">
<style>
  :root {
    --stage: #5f5f5f;
    --brand-blue: #1371b9;
    --brand-blue-deep: #0f63a6;
    --paper: #ffffff;
    --muted-blue: #b9d3ea;
    --rule-grey: #8a8a8a;
    --badge-red: #c0392b;
    --badge-gold: #d4a62a;
    --badge-dark: #2e2e2e;
    --badge-navy: #1f3f7a;
    --text-font: "Roboto", Arial, sans-serif;
  }
  * { box-sizing: border-box; margin: 0; padding: 0; }
  html, body { width: 1200px; height: 1200px; overflow: hidden; }
  body { background: var(--stage); font-family: var(--text-font); position: relative; }

  .side-label {
    position: absolute; top: 100px; width: 488px; text-align: center;
    font-family: "Open Sans", Arial, sans-serif; font-weight: 700; font-size: 38px;
    color: var(--paper); letter-spacing: .5px;
  }
  .side-label--front { left: 84px; }
  .side-label--back { left: 654px; }

  .card {
    position: absolute; top: 209px; width: 488px; height: 823px;
    background: var(--brand-blue); overflow: hidden; text-align: center;
  }
  .card--front { left: 84px; }
  .card--back { left: 654px; }
  .card__shape { position: absolute; inset: 0; width: 488px; height: 823px; }
  .card__line { position: absolute; left: 0; width: 100%; }

  .brand { position: absolute; left: 0; width: 100%; }
  .brand__mark {
    display: block; margin: 0 auto; border-radius: 50%; background: var(--brand-blue);
  }
  .brand__name {
    font-weight: 900; color: var(--brand-blue); letter-spacing: -.5px; line-height: 1;
  }
  .brand__tagline {
    font-weight: 700; color: #555; letter-spacing: .6px; line-height: 1;
  }

  .person__name { top: 446px; font-size: 26px; font-weight: 700; color: var(--paper); letter-spacing: .5px; }
  .person__title { top: 484px; font-size: 19px; font-weight: 400; color: var(--muted-blue); letter-spacing: .4px; }
  .contact__phones { top: 596px; font-size: 19px; font-weight: 700; color: var(--paper); }
  .contact__email { top: 630px; font-size: 19px; color: var(--paper); }
  .contact__web { top: 663px; font-size: 19px; color: var(--paper); }

  .services {
    position: absolute; left: 0; bottom: 0; width: 100%; height: 50px;
    background: var(--paper); color: var(--brand-blue);
    font-size: 16px; font-weight: 700; line-height: 50px; letter-spacing: .2px;
  }

  .headline-strip {
    position: absolute; top: 0; left: 0; width: 100%; height: 52px;
    background: var(--paper); line-height: 52px; font-size: 20px; color: #555; letter-spacing: .3px;
  }
  .headline-strip strong { color: var(--brand-blue-deep); font-weight: 900; }
  .why__title { top: 73px; font-size: 26px; font-weight: 700; color: var(--paper); }
  .why__list { position: absolute; top: 140px; left: 0; width: 100%; list-style: none; }
  .why__item {
    height: 36.5px; line-height: 36.5px; font-size: 17px; color: var(--paper); white-space: nowrap;
  }
  .why__item::before { content: "✓"; font-weight: 700; margin-right: 10px; }
  .reviews__count { top: 392px; font-size: 26px; font-weight: 700; color: var(--paper); }
  .reviews__source { top: 428px; font-size: 19px; font-weight: 700; color: var(--paper); }

  .badges {
    position: absolute; left: 40px; top: 770px; width: 408px;
    display: flex; justify-content: space-between; align-items: center;
  }
  .badge { width: 44px; height: 44px; border-radius: 50%; }
  .badge--rect { width: 56px; height: 34px; border-radius: 3px; }
  .badge--small { width: 30px; height: 30px; }
</style>
</head>
<body>

  <div class="side-label side-label--front">FRONT SIDE</div>
  <div class="side-label side-label--back">BACK SIDE</div>

  <!-- Front of the card -->
  <section class="card card--front">
    <svg class="card__shape" viewBox="0 0 488 823" aria-hidden="true">
      <ellipse cx="300" cy="150" rx="390" ry="215" fill="none" stroke="#ffffff" stroke-width="6" transform="translate(0 26)"/>
      <ellipse cx="300" cy="150" rx="390" ry="200" fill="#ffffff"/>
    </svg>

    <div class="brand" style="top:58px;">
      <span class="brand__mark" style="width:128px;height:128px;"></span>
      <div class="brand__name" style="font-size:40px;margin-top:14px;">KEYSTONE GROUP</div>
      <div class="brand__tagline" style="font-size:13px;margin-top:8px;">INSPECTION PROFESSIONALS</div>
    </div>

    <div class="brand person__name">DANA WHITFIELD</div>
    <div class="brand person__title">CERTIFIED MOLD INSPECTOR</div>

    <div class="brand contact__phones">800.555.0142 | 562.555.0199</div>
    <div class="brand contact__email">dana@keystoneinspections.com</div>
    <div class="brand contact__web">www.KeystoneInspections.com</div>

    <div class="services">HOME ▪ SEWER ▪ MOLD ▪ COMMERCIAL ▪ TERMITE ▪ ROOF</div>
  </section>

  <!-- Back of the card -->
  <section class="card card--back">
    <svg class="card__shape" viewBox="0 0 488 823" aria-hidden="true">
      <ellipse cx="290" cy="790" rx="400" ry="300" fill="none" stroke="#ffffff" stroke-width="6" transform="translate(0 -26)"/>
      <ellipse cx="290" cy="790" rx="400" ry="285" fill="#ffffff"/>
      <line x1="38" y1="747" x2="450" y2="747" stroke="#8a8a8a" stroke-width="1.5"/>
    </svg>

    <div class="headline-strip"><strong>CALIFORNIA'S #1</strong> INSPECTION COMPANY!</div>

    <div class="brand why__title">Why Choose the Keystone Group...</div>
    <ul class="why__list">
      <li class="why__item">Performing Inspections Since 1984</li>
      <li class="why__item">HomeCert Certified Master/ Professional Inspectors®</li>
      <li class="why__item">500,000+ Inspections Completed Statewide</li>
      <li class="why__item">Request of Repairs Pricer Report</li>
      <li class="why__item">90-Day Inspection Guarantees</li>
      <li class="why__item">Federal Drone Licensed Roof Inspectors upon request</li>
    </ul>

    <div class="brand reviews__count">5,000+ 5-Star</div>
    <div class="brand reviews__source">Reviews on Searchly &amp; Rateway</div>

    <div class="brand" style="top:565px;">
      <span class="brand__mark" style="width:86px;height:86px;"></span>
      <div class="brand__name" style="font-size:27px;margin-top:10px;">KEYSTONE GROUP</div>
      <div class="brand__tagline" style="font-size:9px;margin-top:5px;">INSPECTION PROFESSIONALS</div>
    </div>

    <div class="badges">
      <span class="badge" style="background:var(--badge-red);"></span>
      <span class="badge" style="background:var(--badge-gold);"></span>
      <span class="badge" style="background:var(--badge-dark);"></span>
      <span class="badge" style="background:var(--badge-navy);"></span>
      <span class="badge badge--rect" style="background:var(--badge-red);"></span>
      <span class="badge badge--small" style="background:var(--brand-blue);"></span>
    </div>
  </section>

</body>
</html>
```